Visit card

Industry/Entity Type

Health Care

Contact Information for Business Card

O VITALIS SYSTEMS
Odile Brevard - chef de Projet

Requirements
Must have
• 318 Gaston Lemaire Street 59710 BÉTHUNE Tel: 33 (0) 327 481 605 Mobile: 06 42 19 37 64 Web: www.quorvexsystems.example Contact: o.brevard@o-vitalissystems.example
Should not have
• Respect for color

```html
<!DOCTYPE html>
<html lang="en">
<head>
<meta charset="utf-8">
<title>O Vitalis Systems – Business Card</title>
<link rel="stylesheet" href="https://fonts.googleapis.com/css2?family=Arimo:wght@400;700&display=swap">
<style>
  :root {
    --stage: #1e1e21;
    --card-dark: #3c3c3e;
    --card-light: #ffffff;
    --brand-red: #e3202a;
    --ink: #2b2b2b;
  }
  * { box-sizing: border-box; margin: 0; padding: 0; }
  html, body { width: 1200px; height: 800px; overflow: hidden; }
  body {
    background: var(--stage);
    font-family: "Arimo", Arial, sans-serif;
    display: flex;
    align-items: center;
    justify-content: center;
    gap: 50px;
  }
  .card {
    position: relative;
    width: 530px;
    height: 303px;
    overflow: hidden;
    border-radius: 3px;
    box-shadow: 0 18px 40px rgba(0,0,0,.45);
  }
  .card--back { background: var(--card-dark); }
  .card--front { background: var(--card-light); }

  .brand {
    display: flex;
    align-items: center;
    gap: 14px;
  }
  .brand__dot {
    flex: none;
    border-radius: 50%;
  }
  .brand__name {
    font-weight: 700;
    letter-spacing: 1.5px;
    line-height: 1;
    white-space: nowrap;
  }
  .card--back .brand {
    position: absolute;
    left: 0; right: 0; top: 0; bottom: 0;
    justify-content: center;
  }
  .card--back .brand__dot {
    width: 40px; height: 40px;
    background: #fff;
  }
  .card--back .brand__name { color: #fff; font-size: 28px; }

  .card--front .brand {
    position: absolute;
    left: 34px; top: 34px;
    gap: 10px;
  }
  .card--front .brand__dot {
    width: 22px; height: 22px;
    background: var(--ink);
  }
  .card--front .brand__name { color: var(--brand-red); font-size: 22px; }

  .person {
    position: absolute;
    left: 34px; top: 104px;
  }
  .person__name {
    font-size: 17px; font-weight: 700; color: var(--ink);
    letter-spacing: .3px;
  }
  .person__role {
    font-size: 13px; color: var(--brand-red); margin-top: 2px;
  }
  .details {
    position: absolute;
    left: 34px; top: 156px;
    font-size: 11.5px;
    color: var(--ink);
    line-height: 1.45;
  }
  .details__address { margin-bottom: 8px; }
  .contact-list { list-style: none; }
  .contact-list li {
    display: flex; align-items: center; gap: 7px;
    height: 19px;
  }
  .contact-list svg { width: 14px; height: 14px; flex: none; }
  .web { margin-top: 8px; }
  .web__domain { color: var(--brand-red); }
</style>
</head>
<body>

  <section class="card card--back" aria-label="Business card, back">
    <div class="brand">
      <span class="brand__dot" aria-hidden="true"></span>
      <span class="brand__name">O VITALIS SYSTEMS</span>
    </div>
  </section>

  <section class="card card--front" aria-label="Business card, front">
    <div class="brand">
      <span class="brand__dot" aria-hidden="true"></span>
      <span class="brand__name">O VITALIS SYSTEMS</span>
    </div>

    <div class="person">
      <p class="person__name">ODILE BREVARD</p>
      <p class="person__role">chef de Projet</p>
    </div>

    <div class="details">
      <p class="details__address">318 Gaston Lemaire Street<br>59710 BÉTHUNE</p>
      <ul class="contact-list">
        <li>
          <svg viewBox="0 0 14 14" aria-hidden="true"><circle cx="7" cy="7" r="6.2" fill="none" stroke="#e3202a" stroke-width="1.2"/><path d="M4.6 4.2c.4-.4.8-.4 1 0l.6 1c.2.3.1.6-.2.8l-.3.3c.4.8 1 1.4 1.8 1.8l.3-.3c.2-.3.5-.4.8-.2l1 .6c.4.2.4.6 0 1-.6.7-1.4.8-2.3.3A6.5 6.5 0 0 1 4.4 6.5c-.5-.9-.4-1.7.2-2.3z" fill="#e3202a"/></svg>
          33 (0) 327 481 605
        </li>
        <li>
          <svg viewBox="0 0 14 14" aria-hidden="true"><circle cx="7" cy="7" r="6.2" fill="none" stroke="#e3202a" stroke-width="1.2"/><rect x="5" y="3.6" width="4" height="6.8" rx=".7" fill="none" stroke="#e3202a" stroke-width="1"/><circle cx="7" cy="9.2" r=".45" fill="#e3202a"/></svg>
          06 42 19 37 64
        </li>
        <li>
          <svg viewBox="0 0 14 14" aria-hidden="true"><circle cx="7" cy="7" r="6.2" fill="none" stroke="#e3202a" stroke-width="1.2"/><rect x="3.8" y="4.8" width="6.4" height="4.4" rx=".4" fill="#e3202a"/><path d="M3.9 5l3.1 2.3L10.1 5" fill="none" stroke="#fff" stroke-width=".8"/></svg>
          o.brevard@o-vitalissystems.example
        </li>
      </ul>
      <p class="web">www.<span class="web__domain">quorvexsystems</span>.example</p>
    </div>
  </section>

</body>
</html>
```